Business Card Design (NEW FILES)

ATTENTION: New vector files are available. Please update your design to reflect/use the new (better resolution) logo images.

Seeking a unique and professional business card design for a commercial drone photography/videography business. The layout should feature
the logo (attached) and include the following information:
Owen Tarrick
614-502-7738
www.skylarkreelworks.example
NRD Certified Remote Pilot

Owen Tarrick

```html
<!DOCTYPE html>
<html lang="en">
<head>
<meta charset="utf-8">
<title>Skylark Reelworks – Business Card</title>
<link rel="stylesheet" href="https://fonts.googleapis.com/css2?family=Lato:wght@400;700;900&display=swap">
<style>
  :root {
    --backdrop: #8f8f8f;
    --navy: #131a45;
    --white: #ffffff;
    --orange: #ee7f3b;
    --ink: #131a45;
  }
  * { margin: 0; padding: 0; box-sizing: border-box; }
  html, body { width: 1200px; height: 1200px; overflow: hidden; }
  body {
    background: var(--backdrop);
    font-family: "Lato", sans-serif;
    position: relative;
  }
  .card {
    position: absolute;
    left: 281px;
    width: 642px;
    height: 366px;
    border-radius: 19px;
    overflow: hidden;
  }
  .card--front { top: 195px; background: var(--white); }
  .card--back { top: 639px; background: var(--navy); }

  .card__feature {
    position: absolute;
    inset: 0;
    width: 642px;
    height: 366px;
  }

  .wordmark {
    position: absolute;
    font-weight: 700;
    letter-spacing: 0.02em;
    white-space: nowrap;
  }
  .card--front .wordmark {
    left: 42px; top: 62px;
    font-size: 27px;
    color: var(--navy);
  }
  .card--back .wordmark {
    left: 0; right: 0; top: 160px;
    text-align: center;
    font-size: 40px;
    color: var(--white);
  }

  .holder { position: absolute; left: 42px; top: 155px; color: var(--ink); }
  .holder__name { font-size: 27px; font-weight: 900; letter-spacing: 0.01em; line-height: 1; }
  .holder__role { font-size: 17px; color: var(--orange); margin-top: 8px; line-height: 1; }

  .contact { list-style: none; margin-top: 20px; font-size: 15.5px; }
  .contact__item { display: flex; align-items: center; gap: 10px; height: 22px; }
  .contact__icon { width: 13px; height: 13px; fill: var(--navy); }

  .credentials { margin-top: 18px; font-size: 15.5px; line-height: 22px; }
  .credentials__strong { font-weight: 900; letter-spacing: 0.03em; }
</style>
</head>
<body>

  <section class="card card--front" aria-label="Business card front">
    <svg class="card__feature" viewBox="0 0 642 366" aria-hidden="true">
      <rect x="380" y="0" width="262" height="366" fill="var(--navy)"/>
      <circle cx="483" cy="181" r="212" fill="var(--navy)"/>
      <circle cx="483" cy="181" r="175" fill="var(--white)"/>
    </svg>

    <div class="wordmark">Skylark Reelworks</div>

    <div class="holder">
      <h1 class="holder__name">OWEN TARRICK</h1>
      <p class="holder__role">Owner</p>

      <ul class="contact">
        <li class="contact__item">
          <svg class="contact__icon" viewBox="0 0 24 24"><path d="M6.6 10.8a15.1 15.1 0 0 0 6.6 6.6l2.2-2.2a1 1 0 0 1 1-.25 11.4 11.4 0 0 0 3.6.57 1 1 0 0 1 1 1V20a1 1 0 0 1-1 1A17 17 0 0 1 3 4a1 1 0 0 1 1-1h3.5a1 1 0 0 1 1 1c0 1.25.2 2.45.57 3.57a1 1 0 0 1-.25 1z"/></svg>
          <span>614-502-7738</span>
        </li>
        <li class="contact__item">
          <svg class="contact__icon" viewBox="0 0 24 24"><circle cx="12" cy="12" r="10" fill="none" stroke="var(--navy)" stroke-width="2.5"/><path d="M12 2a10 10 0 0 1 0 20M2 12h20" fill="none" stroke="var(--navy)" stroke-width="2.5"/></svg>
          <span>skylarkreelworks.example</span>
        </li>
      </ul>

      <p class="credentials">NRD Certified Remote Pilot<br><span class="credentials__strong">FULLY INSURED</span></p>
    </div>
  </section>

  <section class="card card--back" aria-label="Business card back">
    <div class="wordmark">Skylark Reelworks</div>
  </section>

</body>
</html>
```